Business Card Design for Varomir Facility Services

We are looking for a Business Card Design for the Company "Varomir Facility Services."
Front side:
- Company Logo (small)
- Company Name, address, pohone, website and personal data.
- white background, for text e.g. company colors (blue or green like in the logo)
Please use following data:
Company data:
Varomir Facility Services Kostelac
Birkenhaldweg 14
6341 Lindenau
www.varomir-fs.ch
Person data:
Tarik Kostelac
Geschäftsführer
+41 76 519 47 83
info@varomir-fs.ch
Back side:
could be colored in blue or green
please use a big logo sing and some smaller icons to say what is all beeing offered in facility services, like cleaning, maintenance cleaning
industrial cleaning, caretaking, gardening, disposal. There is no need for everyone of the icons if there are similar or an icon is standing for more of them.
colors to use:
blue: HEX 246BB0
green: HEX 52B33E

```html
<!DOCTYPE html>
<html lang="de">
<head>
<meta charset="utf-8">
<title>Varomir Facility Services – Visitenkarte</title>
<link rel="stylesheet" href="https://fonts.googleapis.com/css2?family=Montserrat:wght@400;500;600&family=Roboto:wght@500&display=swap">
<style>
  :root {
    --brand-blue: #246BB0;
    --card-blue: #2A72B3;
    --brand-green: #52B33E;
    --ink: #3c3c3c;
    --paper: #ffffff;
    --stage: #2b2b2b;
  }
  * { box-sizing: border-box; margin: 0; padding: 0; }
  html, body { width: 1200px; height: 900px; overflow: hidden; }
  body {
    background: var(--stage);
    font-family: "Montserrat", sans-serif;
    position: relative;
  }
  .card {
    position: absolute;
    left: 261px;
    width: 656px;
    height: 357px;
    overflow: hidden;
  }
  .card--front { top: 69px; background: var(--paper); }
  .card--back  { top: 472px; background: var(--card-blue); }

  .wordmark {
    display: flex;
    align-items: center;
    gap: 10px;
    font-family: "Montserrat", sans-serif;
    font-weight: 600;
  }
  .wordmark__dot {
    width: 18px; height: 18px; border-radius: 50%;
    background: var(--brand-green);
    flex: none;
  }
  .card--front .wordmark {
    position: absolute; left: 24px; top: 66px;
    color: var(--brand-blue);
    font-size: 22px;
    letter-spacing: 0.5px;
    width: 230px;
    line-height: 1.25;
  }
  .card--back .wordmark {
    position: absolute; left: 0; right: 0; top: 158px;
    justify-content: center;
    color: var(--paper);
    font-size: 31px;
    letter-spacing: 1px;
  }
  .card--back .wordmark__dot { width: 26px; height: 26px; }

  .person {
    position: absolute; right: 27px; top: 166px;
    text-align: right;
  }
  .person__name {
    font-family: "Roboto", sans-serif;
    font-weight: 500;
    font-size: 25px;
    color: var(--brand-blue);
    line-height: 1.1;
  }
  .person__role {
    font-size: 17px;
    color: var(--ink);
    letter-spacing: 1px;
    margin-top: 3px;
  }
  .divider {
    position: absolute; left: 24px; right: 26px; top: 230px;
    height: 1.5px; background: var(--brand-blue);
  }
  .contact {
    position: absolute; left: 24px; top: 255px;
    list-style: none;
    font-size: 17px; color: var(--ink); letter-spacing: 0.8px;
    line-height: 22px;
  }
  .contact li { display: flex; align-items: center; gap: 8px; }
  .contact svg { width: 12px; height: 12px; flex: none; }
  .contact .accent { color: var(--brand-blue); font-weight: 500; }
  .address {
    position: absolute; right: 26px; top: 255px;
    text-align: right; font-size: 17px; color: var(--ink);
    letter-spacing: 0.8px; line-height: 22px; font-style: normal;
  }
  .wave { position: absolute; left: 0; bottom: 0; width: 656px; height: 357px; }
</style>
</head>
<body>

<section class="card card--front">
  <div class="wordmark"><span class="wordmark__dot"></span><span>Varomir Facility Services</span></div>

  <div class="person">
    <div class="person__name">Tarik Kostelac</div>
    <div class="person__role">Geschäftsführer</div>
  </div>

  <div class="divider"></div>

  <ul class="contact">
    <li>
      <svg viewBox="0 0 12 12"><path d="M3 1.5 L4.5 1 L5.3 3.4 L4.2 4.3 Q5 6.6 7 7.8 L8 6.8 L10.4 7.7 L10 9.3 Q9 10.8 6.8 9.8 Q2.6 7.6 1.9 3.6 Q1.8 2.2 3 1.5 Z" fill="#246BB0"/></svg>
      <span>+41 76 519 47 83</span>
    </li>
    <li>
      <svg viewBox="0 0 12 12"><rect x="1" y="2.5" width="10" height="7" rx="1" fill="none" stroke="#246BB0" stroke-width="1.2"/><path d="M1.5 3 L6 6.5 L10.5 3" fill="none" stroke="#246BB0" stroke-width="1.2"/></svg>
      <span>info@varomir-fs.ch</span>
    </li>
    <li>
      <svg viewBox="0 0 12 12" fill="none" stroke="#246BB0" stroke-width="0.9"><circle cx="6" cy="6" r="4.8"/><ellipse cx="6" cy="6" rx="2" ry="4.8"/><path d="M1.2 6 H10.8 M2 3.5 H10 M2 8.5 H10"/></svg>
      <span>www.<span class="accent">varomir-fs</span>.ch</span>
    </li>
  </ul>

  <address class="address">Birkenhaldweg 14<br>6341 Lindenau</address>

  <svg class="wave" viewBox="0 0 656 357" aria-hidden="true">
    <path d="M0 330 C120 350 240 342 360 325 C440 314 520 300 580 318 C610 327 636 338 656 349 L656 357 L0 357 Z" fill="#246BB0"/>
    <path d="M12 331 C130 352 250 344 360 323 C440 309 520 297 580 312 C605 319 625 330 641 341" fill="none" stroke="#ffffff" stroke-width="7"/>
    <path d="M12 331 C130 350 250 342 360 321 C440 307 520 295 580 310 C605 317 625 328 641 339" fill="none" stroke="#52B33E" stroke-width="4"/>
  </svg>
</section>

<section class="card card--back">
  <div class="wordmark"><span class="wordmark__dot"></span><span>Varomir Facility Services</span></div>
</section>

</body>
</html>
```